Home Loan Introducer needs logo/business cards

We need a simple but classy logo for business cards and flyers. The business is a home loan referral business that is called an Introducer. The business name is "The Harborline".
I was thinking very simple and straight to the point on the front with "Home Loans" the only thing on the front with a nice background colour/s.
Then on the back, "The Harborline"
and "Quality Customer Service"
and "Email, text or call welcome"
and then my name, email address and phone number.
Updates
Thank you for all the designs :-)
Target Market(s)
Home buyers.
Home owners.
Investors.
Industry/Entity Type
Loan
Look and feel

```html
<!DOCTYPE html>
<html lang="en">
<head>
<meta charset="utf-8">
<title>The Harborline – Home Loan Business Cards</title>
<link rel="stylesheet" href="https://fonts.googleapis.com/css2?family=Exo+2:wght@400;600;700&display=swap">
<style>
  :root {
    --brand-blue: #0066b3;
    --brand-orange: #fbab38;
    --paper: #ffffff;
    --backdrop: #e6e7e9;
    --card-shadow: rgba(0, 0, 0, 0.18);
  }
  * { box-sizing: border-box; margin: 0; padding: 0; }
  html, body {
    width: 1200px;
    height: 848px;
    overflow: hidden;
  }
  body {
    background: var(--backdrop);
    font-family: "Exo 2", sans-serif;
    position: relative;
  }
  .card {
    position: absolute;
    top: 154px;
    width: 320px;
    height: 540px;
    overflow: hidden;
    box-shadow: 0 10px 30px var(--card-shadow);
  }

  /* Front */
  .card--front {
    left: 200px;
    background: var(--brand-blue);
  }
  .front-stripe {
    position: absolute;
    left: 116px;
    top: 0;
    width: 94px;
    height: 100%;
    background: var(--paper);
  }
  .front-band {
    position: absolute;
    left: 123px;
    top: 26px;
    width: 80px;
    height: 488px;
    background: var(--brand-orange);
    border-radius: 9px;
    display: flex;
    align-items: center;
    justify-content: center;
  }
  .front-title {
    writing-mode: vertical-rl;
    font-size: 56px;
    font-weight: 700;
    letter-spacing: 2px;
    line-height: 1;
  }
  .front-title__home { color: var(--paper); }
  .front-title__loan { color: var(--brand-blue); }

  /* Back */
  .card--back {
    left: 680px;
    background: var(--paper);
  }
  .back-lower {
    position: absolute;
    left: 0;
    top: 232px;
    width: 100%;
    height: 308px;
    background: linear-gradient(160deg, var(--brand-orange) 55%, #fcc877 85%, var(--brand-orange) 100%);
  }
  .back-rule {
    position: absolute;
    top: 0;
    width: 12px;
    height: 100%;
    background: var(--brand-blue);
  }
  .back-rule--left { left: 46px; }
  .back-rule--right { left: 268px; }
  .brand {
    position: absolute;
    left: 84px;
    top: 34px;
    display: flex;
    flex-direction: row-reverse;
    align-items: flex-start;
    gap: 16px;
  }
  .brand__name {
    writing-mode: vertical-rl;
    color: var(--brand-blue);
    font-size: 22px;
    font-weight: 700;
    letter-spacing: 1px;
    line-height: 1;
  }
  .brand__dot {
    width: 40px;
    height: 40px;
    border-radius: 50%;
    background: var(--brand-blue);
    margin-top: 6px;
  }
  .contact {
    position: absolute;
    right: 66px;
    top: 248px;
    writing-mode: vertical-rl;
    color: var(--paper);
    font-size: 14px;
    font-weight: 400;
    line-height: 1.35;
  }
  .contact__line { display: block; }
  .contact__company {
    font-size: 16px;
    padding-left: 3px;
    border-right: 2px dotted var(--brand-blue);
    padding-right: 3px;
    margin-right: 3px;
    height: 150px;
  }
  .contact__name { font-size: 16px; }
</style>
</head>
<body>
  <section class="card card--front" aria-label="Card front">
    <div class="front-stripe"></div>
    <div class="front-band">
      <h1 class="front-title">
        <span class="front-title__home">HOME</span>
        <span class="front-title__loan">LOAN</span>
      </h1>
    </div>
  </section>

  <section class="card card--back" aria-label="Card back">
    <div class="back-lower"></div>
    <div class="back-rule back-rule--left"></div>
    <div class="back-rule back-rule--right"></div>

    <div class="brand">
      <span class="brand__dot"></span>
      <span class="brand__name">THE HARBORLINE</span>
    </div>

    <address class="contact" style="font-style:normal">
      <span class="contact__line">Quality Customer Service</span>
      <span class="contact__line">Email, text or call are Welcome</span>
      <span class="contact__line contact__company">The Harborline</span>
      <span class="contact__line contact__name">Daniel Crestwood</span>
      <span class="contact__line">daniel@harborlineloans.com</span>
      <span class="contact__line">+61 400 555 218</span>
    </address>
  </section>
</body>
</html>
```